Need business card with a logo for a hearing aid sales and audiology business. We have two Hearing Instrument Specialists and one Audiologist on staff. Over 25 years in business. Locally owned and operated. Financing available. Most insurances accepted.

Summit Audio Wellness LLC
48730 W Larchmont, Suite 7
Spokane, WA 99281
509-617-2084
www.summitaudiowell.example

Manager
Tobias Kerrell HIS COHC
License #71829046

Target Market(s)

50yr old + people with a hearing loss.

Industry/Entity Type

Business

Contact Information for Business Card

48730 W Larchmont, Suite 7
Spokane, WA 99281
509-617-2084
www.summitaudiowell.example

Manager
Tobias Kerrell HIS COHC
NLVE #71829046

Font styles to use
Serif
Sans Serif

Requirements
Must have
• Business name, Tobias's name and title(s) and contact information, License #, web address

```html
<!DOCTYPE html>
<html lang="en">
<head>
<meta charset="utf-8">
<title>Summit Audio Wellness LLC – Business Card</title>
<link rel="stylesheet" href="https://fonts.googleapis.com/css2?family=Alegreya+Sans:ital,wght@0,400;0,500;0,700;1,400&family=Alegreya+Sans+SC:wght@500&display=swap">
<style>
  :root {
    --card-bg: #ffffff;
    --brand-slate: #5877a0;
    --ink-blue: #2c4b9e;
    --title-grey: #5a6f8f;
    --rule-grey: #efefef;
    --band-text: #ffffff;
    --license-text: #dfe6ef;
  }
  * { box-sizing: border-box; }
  html, body {
    margin: 0;
    padding: 0;
    width: 1200px;
    height: 758px;
    overflow: hidden;
    background: var(--card-bg);
  }
  .card {
    position: relative;
    width: 1200px;
    height: 758px;
    overflow: hidden;
    background: var(--card-bg);
    font-family: "Alegreya Sans", sans-serif;
  }
  .card p, .card h1, .card address { margin: 0; }
  .brand-square {
    position: absolute;
    left: 41px;
    top: 0;
    width: 198px;
    height: 266px;
    background: var(--brand-slate);
  }
  .company-name {
    position: absolute;
    left: 275px;
    top: 80px;
    font-size: 70px;
    font-weight: 700;
    line-height: 1;
    color: var(--brand-slate);
    letter-spacing: -0.5px;
    white-space: nowrap;
  }
  .header-rule {
    position: absolute;
    left: 314px;
    top: 179px;
    width: 776px;
    height: 4px;
    background: var(--rule-grey);
  }
  .person-name, .person-title {
    position: absolute;
    left: 0;
    width: 1200px;
    text-align: center;
    line-height: 1;
    white-space: nowrap;
  }
  .person-name {
    top: 337px;
    font-size: 60px;
    font-weight: 700;
    color: var(--ink-blue);
    letter-spacing: -0.5px;
  }
  .person-title {
    top: 394px;
    font-family: "Alegreya Sans SC", sans-serif;
    font-weight: 500;
    font-size: 40px;
    color: var(--title-grey);
    letter-spacing: 1px;
  }
  .contact-icon {
    position: absolute;
    fill: var(--ink-blue);
  }
  .icon-home { left: 87px; top: 551px; width: 54px; height: 50px; }
  .icon-phone { left: 673px; top: 557px; width: 56px; height: 44px; }
  .contact-text {
    position: absolute;
    font-family: "Alegreya Sans SC", sans-serif;
    font-weight: 500;
    font-size: 40px;
    line-height: 45px;
    color: var(--ink-blue);
    font-style: normal;
    white-space: nowrap;
  }
  .address { left: 171px; top: 558px; }
  .telephone { left: 766px; top: 558px; }
  .footer-band {
    position: absolute;
    left: 0;
    top: 690px;
    width: 1200px;
    height: 68px;
    background: var(--brand-slate);
  }
  .license {
    position: absolute;
    left: 23px;
    top: 23px;
    font-style: italic;
    font-size: 26px;
    line-height: 1;
    color: var(--license-text);
    white-space: nowrap;
  }
  .website {
    position: absolute;
    right: 30px;
    top: 18px;
    font-size: 40px;
    line-height: 1;
    color: var(--band-text);
    white-space: nowrap;
  }
</style>
</head>
<body>
  <main class="card">
    <div class="brand-square" aria-hidden="true"></div>
    <h1 class="company-name">Summit Audio Wellness LLC</h1>
    <div class="header-rule"></div>

    <p class="person-name">Tobias Kerrell HIS COHC</p>
    <p class="person-title">Manager</p>

    <svg class="contact-icon icon-home" viewBox="0 0 54 50" aria-hidden="true">
      <path d="M27 2 L2 24 L8 24 L8 48 L21 48 L21 34 L33 34 L33 48 L46 48 L46 24 L52 24 Z"/>
    </svg>
    <address class="contact-text address">48730 W Larchmont, Suite 7<br>Spokane, WA 99281</address>

    <svg class="contact-icon icon-phone" viewBox="0 0 56 44" aria-hidden="true">
      <path d="M4 14 C4 4 52 4 52 14 L52 18 L40 18 L40 12 C34 10 22 10 16 12 L16 18 L4 18 Z"/>
      <path d="M14 20 L42 20 L50 42 L6 42 Z"/>
      <g fill="#ffffff">
        <rect x="22" y="25" width="3" height="3"/><rect x="27" y="25" width="3" height="3"/><rect x="32" y="25" width="3" height="3"/>
        <rect x="22" y="30" width="3" height="3"/><rect x="27" y="30" width="3" height="3"/><rect x="32" y="30" width="3" height="3"/>
        <rect x="22" y="35" width="3" height="3"/><rect x="27" y="35" width="3" height="3"/><rect x="32" y="35" width="3" height="3"/>
      </g>
    </svg>
    <p class="contact-text telephone">Tel: 509-617-2084</p>

    <footer class="footer-band">
      <p class="license">(NLVE #71829046)</p>
      <p class="website">www.summitaudiowell.example</p>
    </footer>
  </main>
</body>
</html>
```